Need Help having my business card stand out

I am the owner of Birchway Canine Training and would like for my business cards to stand out. I have been trying to keep designing them myself but I can't get what I have in my head on the card. I will try my best to post templates that I like for inspirations. I want something unique but elegant. I don't want in to look cartoony or cheesy. It needs to pop in a pet shop but also in a coffee shop or gym.

Target Market(s)

Dog owners, Married ,No young kids Jr High school kids and up (maybe kids on the way) Executives, Stay at home moms/wives, Small business owners

Industry/Entity Type

Dog Training

Contact Information for Business Card

Lowell Spratt, 281-904-3376, info@birchwaycanine.example, www.birchwaycanine.example

Colors

Designer to choose colors to be used in the design.

Requirements
Must have
• my logo
Should not have
• Cursive lettering

```html
<!DOCTYPE html>
<html lang="en">
<head>
<meta charset="utf-8">
<title>Birchway Canine Training – Business Card</title>
<link href="https://fonts.googleapis.com/css2?family=Open+Sans:ital,wght@0,400;0,600;0,800;1,600;1,700&display=swap" rel="stylesheet">
<style>
  :root {
    --backdrop: #2c2c2c;
    --card-grey: #4b4b4b;
    --card-grey-light: #565656;
    --ink: #0b0b0b;
    --strip: #2f2f2f;
    --accent: #1fae5b;
    --accent-dark: #0f6b34;
    --text-light: #f2f2f2;
  }
  * { box-sizing: border-box; margin: 0; padding: 0; }
  html, body { width: 1200px; height: 900px; overflow: hidden; }
  body {
    background: var(--backdrop);
    font-family: "Open Sans", Arial, sans-serif;
    position: relative;
  }
  .card {
    position: absolute;
    left: 250px;
    width: 700px;
    height: 400px;
    overflow: hidden;
    box-shadow: 0 14px 30px rgba(0,0,0,.55);
  }
  .card--front { top: 30px; }
  .card--back { top: 470px; }
  .card__art { position: absolute; inset: 0; }

  .brand {
    position: absolute;
    display: flex;
    align-items: center;
    gap: 12px;
    color: var(--ink);
    font-weight: 800;
    line-height: 1.05;
  }
  .brand__dot {
    flex: none;
    width: 22px; height: 22px;
    border-radius: 50%;
    background: var(--ink);
  }
  .card--front .brand { left: 330px; top: 120px; width: 320px; font-size: 36px; }
  .card--back .brand { left: 510px; top: 150px; width: 175px; font-size: 26px; gap: 10px; }
  .card--back .brand__dot { width: 18px; height: 18px; }

  .holder {
    position: absolute;
    left: 90px;
    top: 118px;
  }
  .holder__name {
    color: var(--text-light);
    font-size: 30px;
    font-weight: 700;
    font-style: italic;
    letter-spacing: -.3px;
  }
  .holder__role {
    color: var(--accent);
    font-size: 17px;
    font-weight: 600;
    font-style: italic;
    margin-top: -2px;
  }
  .contacts {
    position: absolute;
    left: 70px;
    top: 218px;
    width: 425px;
    display: grid;
    grid-template-columns: 218px 1fr;
    row-gap: 20px;
    color: var(--text-light);
    font-size: 12px;
  }
  .contacts__item { display: flex; align-items: center; gap: 9px; white-space: nowrap; }
  .contacts__item--wide { grid-column: 1 / span 2; }
  .icon {
    flex: none;
    width: 20px; height: 17px;
    background: var(--accent);
    border-radius: 2px;
    display: flex; align-items: center; justify-content: center;
  }
  .icon svg { width: 13px; height: 13px; }
</style>
</head>
<body>

<section class="card card--front" aria-label="Business card front">
  <svg class="card__art" viewBox="0 0 700 400" aria-hidden="true">
    <defs>
      <radialGradient id="frontGrey" cx="55%" cy="35%" r="75%">
        <stop offset="0" stop-color="#595959"/>
        <stop offset="1" stop-color="#424242"/>
      </radialGradient>
      <linearGradient id="badgeGreen" x1="0" y1="0" x2="0" y2="1">
        <stop offset="0" stop-color="#3fd27c"/>
        <stop offset="1" stop-color="#0c5e2c"/>
      </linearGradient>
    </defs>
    <rect width="700" height="400" fill="url(#frontGrey)"/>
    <polygon class="band band--top" points="370,0 700,0 700,60" fill="var(--ink)"/>
    <polygon class="band band--bottom" points="0,305 470,400 0,400" fill="var(--ink)"/>
    <path class="strip" d="M158 0 H230 V225 a8 8 0 0 1 -8 8 H166 a8 8 0 0 1 -8 -8 Z" fill="var(--strip)"/>
    <ellipse class="badge" cx="194" cy="182" rx="33" ry="24" fill="#0a0a0a"/>
    <ellipse class="badge" cx="194" cy="182" rx="29" ry="20.5" fill="url(#badgeGreen)"/>
  </svg>
  <div class="brand"><span class="brand__dot"></span><span>Birchway Canine Training</span></div>
</section>

<section class="card card--back" aria-label="Business card back">
  <svg class="card__art" viewBox="0 0 700 400" aria-hidden="true">
    <defs>
      <radialGradient id="backGrey" cx="45%" cy="40%" r="75%">
        <stop offset="0" stop-color="#5a5a5a"/>
        <stop offset="1" stop-color="#434343"/>
      </radialGradient>
    </defs>
    <rect width="700" height="400" fill="url(#backGrey)"/>
    <polygon class="band band--top" points="300,0 700,0 700,75" fill="var(--ink)"/>
    <polygon class="band band--bottom" points="0,308 0,400 390,400" fill="var(--ink)"/>
  </svg>

  <div class="holder">
    <h1 class="holder__name">Lowell Spratt</h1>
    <p class="holder__role">Designation</p>
  </div>

  <div class="contacts">
    <div class="contacts__item contacts__item--wide">
      <span class="icon"><svg viewBox="0 0 12 12"><path d="M6 1a3.5 3.5 0 0 0-3.5 3.5C2.5 7.5 6 11 6 11s3.5-3.5 3.5-6.5A3.5 3.5 0 0 0 6 1Zm0 5a1.4 1.4 0 1 1 0-2.8A1.4 1.4 0 0 1 6 6Z" fill="#111"/></svg></span>
      <span>48 Alder Lane, Suite 300, Brookfield, US 0000</span>
    </div>
    <div class="contacts__item">
      <span class="icon"><svg viewBox="0 0 12 12"><path d="M2 4c0-1.5 8-1.5 8 0v1H8V4H4v1H2Zm1 2h6l1 4H2Z" fill="#111"/></svg></span>
      <span>281-904-3376</span>
    </div>
    <div class="contacts__item">
      <span class="icon"><svg viewBox="0 0 12 12"><rect x="2" y="2" width="8" height="4" fill="#111"/><rect x="1.5" y="6.5" width="9" height="4" fill="#111"/></svg></span>
      <span>281-904-3377</span>
    </div>
    <div class="contacts__item">
      <span class="icon"><svg viewBox="0 0 12 12"><rect x="1.5" y="3" width="9" height="6.5" fill="none" stroke="#111"/><path d="M1.5 3 6 7l4.5-4" fill="none" stroke="#111"/></svg></span>
      <span>info@birchwaycanine.example</span>
    </div>
    <div class="contacts__item">
      <span class="icon"><svg viewBox="0 0 12 12"><circle cx="6" cy="6" r="4.5" fill="none" stroke="#111"/><path d="M1.5 6h9M6 1.5v9M3.5 3.2c1.6 1 3.4 1 5 0M3.5 8.8c1.6-1 3.4-1 5 0" fill="none" stroke="#111" stroke-width=".8"/></svg></span>
      <span>www.birchwaycanine.example</span>
    </div>
  </div>

  <div class="brand"><span class="brand__dot"></span><span>Birchway Canine Training</span></div>
</section>

</body>
</html>
```